Redesign of business card for Cedar Ridge Mechanical

We are looking for a new design for our business cards for Cedar Ridge Mechanical. We are a plumbing & HVAC construction company, operating on the West Coast of Canada and USA. Logo attached.
Industry/Entity Type
Construction - Plumbing & HVAC
Contact Information for Business Card
Name, address, phone numbers, email, website address
Look and feel
Each slider illustrates characteristics of the customer's brand and the style your logo design should communicate.

```html
<!DOCTYPE html>
<html lang="en">
<head>
<meta charset="utf-8">
<title>Cedar Ridge Mechanical — Business Card</title>
<link rel="stylesheet" href="https://fonts.googleapis.com/css2?family=Montserrat:wght@400;700&display=swap">
<style>
  :root {
    --stage: #232323;
    --card: #141414;
    --card-edge: #ffffff;
    --pattern-light: #5a5a5a;
    --pattern-dark: #0c0c0c;
    --ink: #ffffff;
    --ink-soft: #e6e6e6;
  }
  * { margin: 0; padding: 0; box-sizing: border-box; }
  html, body {
    width: 1200px; height: 780px; overflow: hidden;
    background: var(--stage);
    font-family: "Montserrat", Arial, sans-serif;
    color: var(--ink);
  }
  .canvas { position: relative; width: 1200px; height: 780px; }

  .card {
    position: absolute;
    width: 560px; height: 320px;
    border-radius: 22px;
    background: var(--card);
    border: 2px solid var(--card-edge);
    overflow: hidden;
    box-shadow: 0 18px 40px rgba(0,0,0,.55);
  }

  /* Front */
  .card-front { left: 120px; top: 50px; }
  .front-pattern {
    position: absolute; inset: 0;
    background: linear-gradient(115deg, var(--pattern-light) 0%, #2b2b2b 40%, var(--pattern-dark) 75%);
  }
  .front-brand {
    position: absolute; inset: 0;
    display: flex; align-items: center; justify-content: center; gap: 14px;
  }
  .brand-mark { width: 26px; height: 26px; background: var(--ink); }
  .brand-name {
    font-weight: 700; font-size: 30px; letter-spacing: .5px;
    text-transform: uppercase; color: var(--ink);
  }

  /* Back */
  .card-back { left: 520px; top: 410px; }
  .back-brand {
    position: absolute; left: 34px; top: 0; bottom: 0; width: 230px;
    display: flex; align-items: center; gap: 10px;
  }
  .back-brand .brand-mark { width: 18px; height: 18px; flex: none; }
  .back-brand .brand-name { font-size: 19px; line-height: 1.25; }
  .divider {
    position: absolute; left: 282px; top: 70px; width: 2px; height: 180px;
    background: var(--ink);
  }
  .contact {
    position: absolute; left: 306px; top: 62px; right: 20px;
  }
  .person-name { font-weight: 700; font-size: 22px; letter-spacing: .5px; }
  .person-role { font-size: 13px; color: var(--ink-soft); margin-top: 2px; }
  .address { font-size: 13px; line-height: 1.4; color: var(--ink-soft); margin-top: 14px; }
  .contact-list { list-style: none; margin-top: 12px; }
  .contact-list li {
    display: flex; align-items: center; gap: 8px;
    font-size: 13px; line-height: 1.75; color: var(--ink-soft);
  }
  .contact-list svg { width: 13px; height: 13px; flex: none; fill: var(--ink); }
</style>
</head>
<body>
<main class="canvas">

  <section class="card card-front">
    <div class="front-pattern" role="img" aria-label="Faint repeating brand pattern fading from grey to black"></div>
    <div class="front-brand">
      <span class="brand-mark"></span>
      <span class="brand-name">Cedar Ridge Mechanical</span>
    </div>
  </section>

  <section class="card card-back">
    <div class="back-brand">
      <span class="brand-mark"></span>
      <span class="brand-name">Cedar Ridge Mechanical</span>
    </div>
    <div class="divider"></div>
    <div class="contact">
      <h1 class="person-name">DANIEL MORROW</h1>
      <p class="person-role">Managing Director</p>
      <p class="address">Your address, City<br>State, Zip 1234</p>
      <ul class="contact-list">
        <li>
          <svg viewBox="0 0 16 16" aria-hidden="true"><path d="M3.5 1.5l2.5 0 1.2 3.2-1.6 1.1c.8 1.8 2.2 3.2 4 4l1.1-1.6 3.2 1.2 0 2.5c0 .8-.7 1.5-1.5 1.5C6.6 13.4 2.6 9.4 2 3 2 2.2 2.7 1.5 3.5 1.5z"/></svg>
          123 456 789
        </li>
        <li>
          <svg viewBox="0 0 16 16" aria-hidden="true"><path d="M1 3h14v10H1z M2.5 4.5L8 8.5l5.5-4v-.1H2.5z" fill-rule="evenodd"/></svg>
          info@yourgmail.com
        </li>
        <li>
          <svg viewBox="0 0 16 16" aria-hidden="true"><path d="M8 1a7 7 0 100 14A7 7 0 008 1zm0 1.5c.9 0 1.8 2 2 4.5H6c.2-2.5 1.1-4.5 2-4.5zM2.6 7h2c.1-1.7.5-3.1 1-4.1A5.5 5.5 0 002.6 7zm8.8 0h2a5.5 5.5 0 00-3-4.1c.5 1 .9 2.4 1 4.1zM2.6 9a5.5 5.5 0 003 4.1c-.5-1-.9-2.4-1-4.1zm3.4 0c.2 2.5 1.1 4.5 2 4.5s1.8-2 2-4.5zm5.4 0c-.1 1.7-.5 3.1-1 4.1a5.5 5.5 0 003-4.1z"/></svg>
          www.yourwebsite.com
        </li>
      </ul>
    </div>
  </section>

</main>
</body>
</html>
```